Business Card for a New Zealand IT Startup

I need a business card for VELTA Holdings. We are a young startup based in New Zealand working in internet marketing and web development. The design should have some element connected to New Zealand, such as wave, koru or silver fern, just don't use a kiwi bird.

```html
<!DOCTYPE html>
<html lang="en">
<head>
<meta charset="utf-8">
<title>VELTA Holdings — Business Card</title>
<link href="https://fonts.googleapis.com/css2?family=Montserrat:wght@600;700&family=Open+Sans:wght@400;600&display=swap" rel="stylesheet">
<style>
  :root {
    --brand-blue: #0a6cc0;
    --brand-blue-deep: #075ba6;
    --brand-orange: #ee5a22;
    --paper: #ffffff;
    --backdrop: #2b2c2e;
  }
  html, body {
    margin: 0;
    width: 1200px;
    height: 1000px;
    overflow: hidden;
    background: var(--backdrop);
  }
  .card {
    position: absolute;
    left: 250px;
    width: 700px;
    height: 400px;
    overflow: hidden;
    box-shadow: 0 10px 30px rgba(0,0,0,.45);
  }
  .card--back { top: 60px; background: var(--brand-blue); }
  .card--front { top: 540px; background: var(--paper); }

  .back-brand {
    position: absolute;
    inset: 0;
    display: flex;
    flex-direction: column;
    align-items: center;
    justify-content: center;
    gap: 22px;
  }
  .back-brand__dot {
    width: 150px;
    height: 150px;
    border-radius: 50%;
    background: var(--paper);
  }
  .back-brand__name {
    font-family: 'Montserrat', sans-serif;
    font-weight: 700;
    font-size: 30px;
    letter-spacing: 3px;
    color: var(--paper);
  }

  .front-art { position: absolute; inset: 0; }

  .holder {
    position: absolute;
    left: 42px;
    top: 28px;
    font-family: 'Open Sans', sans-serif;
  }
  .holder__name {
    margin: 0;
    font-weight: 600;
    font-size: 19px;
    color: var(--brand-blue);
    line-height: 1.1;
  }
  .holder__role {
    margin: 0;
    font-size: 15px;
    color: var(--brand-orange);
    letter-spacing: .5px;
  }

  .brand {
    position: absolute;
    left: 90px;
    top: 110px;
    display: flex;
    align-items: center;
    gap: 16px;
  }
  .brand__name {
    font-family: 'Montserrat', sans-serif;
    font-weight: 700;
    font-size: 58px;
    color: var(--brand-blue);
    letter-spacing: 2px;
  }
  .brand__dot {
    width: 44px;
    height: 44px;
    border-radius: 50%;
    background: var(--brand-blue);
  }

  .contact {
    position: absolute;
    right: 30px;
    bottom: 26px;
    margin: 0;
    padding: 0;
    list-style: none;
    font-family: 'Open Sans', sans-serif;
    font-size: 17px;
    color: var(--paper);
    text-align: right;
    line-height: 24px;
  }
  .contact__item {
    display: flex;
    justify-content: flex-end;
    align-items: center;
    gap: 10px;
  }
  .contact__icon { width: 16px; height: 16px; flex: none; }
  .contact__item--address { padding-right: 26px; }
</style>
</head>
<body>

<section class="card card--back" aria-label="Card back">
  <div class="back-brand">
    <span class="back-brand__dot"></span>
    <span class="back-brand__name">VELTA Holdings</span>
  </div>
</section>

<section class="card card--front" aria-label="Card front">
  <svg class="front-art" viewBox="0 0 700 400" preserveAspectRatio="none" aria-hidden="true">
    <path d="M612,0 L700,0 L700,400 L0,400 L0,322 C120,282 250,292 400,294 C540,296 600,230 612,0 Z" fill="var(--brand-blue)"/>
    <path d="M30,318 C150,268 270,270 400,272 C520,274 580,220 600,100 C598,230 540,288 400,290 C260,290 140,286 30,318 Z" fill="var(--brand-orange)"/>
  </svg>

  <div class="holder">
    <p class="holder__name">MARA TANE</p>
    <p class="holder__role">PRESIDENT</p>
  </div>

  <div class="brand">
    <span class="brand__name">VELTA Holdings</span>
    <span class="brand__dot"></span>
  </div>

  <ul class="contact">
    <li class="contact__item">021 555 0148
      <svg class="contact__icon" viewBox="0 0 16 16"><path d="M3 2h3l1 3-2 1a8 8 0 0 0 5 5l1-2 3 1v3a1 1 0 0 1-1 1A13 13 0 0 1 2 3a1 1 0 0 1 1-1z" fill="#fff"/></svg></li>
    <li class="contact__item">022 555 0193
      <svg class="contact__icon" viewBox="0 0 16 16"><rect x="4" y="1" width="8" height="14" rx="1.5" fill="none" stroke="#fff" stroke-width="1.6"/><circle cx="8" cy="12.5" r="1" fill="#fff"/></svg></li>
    <li class="contact__item">09 555 0127
      <svg class="contact__icon" viewBox="0 0 16 16"><rect x="4" y="1" width="8" height="5" fill="none" stroke="#fff" stroke-width="1.4"/><rect x="1" y="6" width="14" height="8" rx="1" fill="#fff"/></svg></li>
    <li class="contact__item">mara@veltaholdings.com
      <svg class="contact__icon" viewBox="0 0 16 16"><rect x="1" y="3" width="14" height="10" fill="#fff"/><path d="M1 3l7 6 7-6" fill="none" stroke="var(--brand-blue)" stroke-width="1.3"/></svg></li>
    <li class="contact__item">www.veltaholdings.com
      <svg class="contact__icon" viewBox="0 0 16 16"><circle cx="8" cy="8" r="7" fill="#fff"/><path d="M1 8h14M8 1c-3 3-3 11 0 14M8 1c3 3 3 11 0 14" fill="none" stroke="var(--brand-blue)" stroke-width="1"/></svg></li>
    <li class="contact__item contact__item--address">42 Harbour View Road Wellington 6011</li>
  </ul>
</section>

</body>
</html>
```